Full 10+ Page Online Learning eBook Design - NOT just the cover :)

We currently have an eBook within the online learning space which is geared towards a consumer audience (hobbyists, interests), but we have a new 2.0 version which is geared towards professionals (certifications, training, continuing ed, career-oriented). We need a new design and need the words/copy put into the eBook, but want to keep the look and feel of the original (open to variations in design). File is attached, along with various logo options.

Target Market(s)

Professionals

Industry/Entity Type

Learning

Font styles to use
Sans Serif

Colors
33a6d7
acd036
919191

Requirements
Must have
• Must follow a very similar look a feel of the original file. We use a lot of fonts like Raleway, Gotham, Helvetica Neue, Gil Sans, DIN - anything modern looking. We also use a lot of grayish hexagons in our corporate design. Feel free to check out brightlanternhub.example to get a better sense.
Nice to have
• Include some professionally oriented icons / photos
Should not have
• No cartoonish graphics or imagery

```html
<!DOCTYPE html>
<html lang="en">
<head>
<meta charset="utf-8">
<title>The Evolution of Online Learning</title>
<link rel="stylesheet" href="https://fonts.googleapis.com/css2?family=Didact+Gothic&display=swap">
<style>
  :root {
    --band-grey: #919191;
    --accent-blue: #33a6d7;
    --ink: #1a1a1a;
    --paper: #ffffff;
    --hex-tint: #d6edf7;
  }
  * { margin: 0; padding: 0; box-sizing: border-box; }
  html, body { width: 852px; height: 1200px; overflow: hidden; background: var(--paper); }
  .page {
    position: relative;
    width: 852px;
    height: 1200px;
    background: var(--paper);
    font-family: "Didact Gothic", "Century Gothic", sans-serif;
    color: var(--ink);
  }
  .band { position: absolute; left: 0; width: 852px; background: var(--band-grey); }
  .band--top { top: 0; height: 19px; }
  .band--under-photo { top: 502px; height: 20px; }
  .band--bottom { top: 1181px; height: 19px; }
  .hero-photo {
    position: absolute;
    top: 19px; left: 0;
    width: 852px; height: 483px;
    background:
      radial-gradient(ellipse 70px 40px at 52% 67%, rgba(255,190,90,0.55), transparent 70%),
      radial-gradient(ellipse 60px 30px at 37% 68%, rgba(230,60,50,0.5), transparent 70%),
      radial-gradient(ellipse 120px 200px at 88% 35%, rgba(230,70,50,0.35), transparent 70%),
      radial-gradient(ellipse 160px 220px at 10% 35%, rgba(40,150,120,0.45), transparent 70%),
      radial-gradient(ellipse 140px 180px at 55% 20%, rgba(70,160,200,0.35), transparent 70%),
      linear-gradient(180deg, #0d1c24 0%, #1a2a2e 45%, #141a1e 70%, #0c1014 100%);
  }
  .section {
    position: absolute;
    top: 545px; left: 7px;
    width: 840px;
  }
  .section__title {
    font-size: 15px;
    font-weight: 400;
    letter-spacing: 0.2px;
    line-height: 18px;
  }
  .section__rule {
    width: 563px;
    height: 3px;
    background: var(--accent-blue);
    margin: 4px 0 12px;
  }
  .section__body p {
    font-size: 14.4px;
    line-height: 18.6px;
    margin-bottom: 18px;
  }
  .hex-field {
    position: absolute;
    right: 0; bottom: 19px;
    width: 430px; height: 300px;
    background: radial-gradient(ellipse 90% 90% at 100% 100%, var(--hex-tint), rgba(214,237,247,0) 75%);
  }
</style>
</head>
<body>
<div class="page">
  <div class="band band--top"></div>
  <div class="hero-photo" role="img" aria-label="Blurred night city street with glowing shop signs and car headlights on wet asphalt"></div>
  <div class="band band--under-photo"></div>

  <section class="section">
    <h1 class="section__title">THE EVOLUTION OF ONLINE LEARNING</h1>
    <div class="section__rule"></div>
    <div class="section__body">
      <p>Companies that are ripe for setting up an online professional learning operation tend to fall into one of three<br>categories:</p>
      <p>• Those with learning content being used for educational purposes that they've been delivering in person or as part<br>of webinars or ebooks. This group needs a better way to distribute, manage and monetize their assets.</p>
      <p>• Those that already work with anLMS (learning management system) but are finding that it no longer scales<br>sufficiently or offers the ecommerce or monetization functionality required to turn the courses into profit-generating<br>programs.</p>
      <p>• Those that have built a learning management system in house but now lack the resources for regular updates or<br>can no longer support it to the scale required.</p>
      <p>In all of these scenarios a major factor for change is to accommodate the shift to mobile learning. According to<br>our own data, 55 percent of the millions of users on our learning platform use it from a tablet or smartphone.<br>For some of our clients 80 percent of their customers are working from a mobile device, depending on the context<br>and content. Today's customer is learning on the go in short form, as we'll discuss next.</p>
    </div>
  </section>

  <div class="hex-field" role="img" aria-label="Faint pale blue hexagon pattern decoration"></div>
  <div class="band band--bottom"></div>
</div>
</body>
</html>
```